Business Card Design

Hi I need a business card designed, we already have the business name logo artwork and would like some concept ideas for the Bus Card layout.
On the back of the card i want to include the products and services that we offer.
We are a Plastics Sheeting manufacture based in Perth Australia.

                                       

We need a BC design for a company called Tarvo Plastics based in Perth Australia.

We supply from DIY to Trade & Industrial  Engineering Markets.

We specialise in:

·         Cut to size panels  (all shapes and sizes)

·         Plastics fabrication & Welding

·         Custom Designs

·         Plastic Repairs

·         PVC Pipe Slotting & PVC Pipe Threading

·         Supplier of all types of engineering plastics and profiles.

Including:           Acrylic / Clarvene

                               Polycarbonate / Dorvil

                               Prismatic Light Diffuser

                               Vantrib

                               HDPE / UHMWPE

                               PVC / PVC Foam

                               Nylon

                               HIPS

```html
<!DOCTYPE html>
<html lang="en">
<head>
<meta charset="utf-8">
<title>Tarvo Plastics – Business Card</title>
<link href="https://fonts.googleapis.com/css2?family=Open+Sans:wght@400;600;700;800&display=swap" rel="stylesheet">
<style>
  :root {
    --navy: #1f2a5c;
    --blue: #2f8bcb;
    --orange: #f08a1c;
    --grey-text: #4a4a4a;
    --rule: #c9cdd6;
    --white: #ffffff;
    --stage: #e9e7e3;
  }
  * { box-sizing: border-box; margin: 0; padding: 0; }
  html, body { width: 1200px; height: 720px; overflow: hidden; }
  body {
    background: var(--stage);
    font-family: "Open Sans", Arial, sans-serif;
    position: relative;
  }
  .card {
    position: absolute;
    top: 195px;
    width: 540px;
    height: 330px;
    border-radius: 4px;
    box-shadow: 0 6px 18px rgba(0,0,0,0.18);
    overflow: hidden;
  }

  /* Front */
  .card-front { left: 40px; background: var(--white); }
  .brand-front {
    position: absolute; top: 46px; left: 140px;
    display: flex; align-items: center; gap: 12px;
  }
  .brand-mark { width: 26px; height: 26px; background: var(--navy); }
  .brand-name {
    font-weight: 800; font-size: 44px; color: var(--navy);
    letter-spacing: -0.5px; line-height: 1;
  }
  .identity {
    position: absolute; top: 140px; left: 40px; width: 228px;
    text-align: right; color: var(--grey-text);
  }
  .person-name { font-weight: 700; font-size: 17px; color: var(--navy); line-height: 1.1; }
  .person-title { font-weight: 600; font-size: 12px; color: var(--orange); margin-bottom: 10px; }
  .address { font-size: 13.5px; line-height: 1.35; }
  .divider-front {
    position: absolute; top: 132px; left: 284px; width: 1px; height: 120px;
    background: var(--rule);
  }
  .contacts {
    position: absolute; top: 132px; left: 300px; list-style: none;
    font-size: 13.5px; color: var(--grey-text);
  }
  .contacts li { display: flex; align-items: center; gap: 8px; height: 25px; }
  .contacts svg { width: 14px; height: 14px; fill: var(--orange); flex: none; }
  .footer-rule {
    position: absolute; left: 0; right: 0; bottom: 58px; height: 4px; background: var(--navy);
  }
  .footer-band {
    position: absolute; left: 0; right: 0; bottom: 0; height: 48px;
    background: var(--navy); color: var(--white);
    display: flex; align-items: center; justify-content: center;
    font-size: 13px; font-weight: 600;
  }

  /* Back */
  .card-back { left: 620px; background: var(--blue); color: var(--white); }
  .brand-back {
    position: absolute; top: 26px; left: 0; right: 0;
    display: flex; justify-content: center; align-items: center; gap: 12px;
  }
  .brand-back .brand-mark { background: var(--white); }
  .brand-back .brand-name { color: var(--white); font-size: 42px; }
  .headline {
    position: absolute; top: 92px; left: 0; right: 0; text-align: center;
    font-weight: 700; font-size: 14px; line-height: 1.3;
  }
  .offer-col { position: absolute; top: 142px; }
  .offer-col h2 { font-weight: 700; font-size: 17px; margin-bottom: 4px; }
  .offer-col ul { list-style: none; font-size: 12.5px; line-height: 1.38; }
  .offer-col li { position: relative; padding-left: 12px; }
  .offer-col li::before {
    content: ""; position: absolute; left: 0; top: 7px;
    width: 5px; height: 5px; border-radius: 50%; background: var(--white);
  }
  .services { left: 26px; width: 300px; }
  .materials { left: 360px; width: 170px; }
  .divider-back {
    position: absolute; top: 148px; left: 344px; width: 1px; height: 150px;
    background: rgba(255,255,255,0.55);
  }
</style>
</head>
<body>

<section class="card card-front" aria-label="Business card front">
  <div class="brand-front">
    <span class="brand-mark"></span>
    <span class="brand-name">Tarvo Plastics</span>
  </div>

  <div class="identity">
    <p class="person-name">Your Name</p>
    <p class="person-title">Title</p>
    <p class="address">Unit 4/18 Brennick Circuit<br>Marlow Vale WA 6318<br>PO Box 2240<br>Marlow Vale DC WA 6992</p>
  </div>

  <div class="divider-front"></div>

  <ul class="contacts">
    <li><svg viewBox="0 0 16 16" aria-hidden="true"><path d="M3.5 1.5l2.5 0 1 3.5-1.8 1.2a8 8 0 0 0 4.6 4.6L11 9l3.5 1v2.5c0 1-1 2-2 2A11 11 0 0 1 1.5 3.5c0-1 1-2 2-2z"/></svg>08 9000 4811</li>
    <li><svg viewBox="0 0 16 16" aria-hidden="true"><path d="M5 1h6a1 1 0 0 1 1 1v12a1 1 0 0 1-1 1H5a1 1 0 0 1-1-1V2a1 1 0 0 1 1-1zm0.8 2v8.5h4.4V3zM8 12.3a.9.9 0 1 0 0 1.8.9.9 0 0 0 0-1.8z"/></svg>0400 555 019</li>
    <li><svg viewBox="0 0 16 16" aria-hidden="true"><path d="M4 1h8v4H4zM2 6h12a1 1 0 0 1 1 1v5h-3v3H4v-3H1V7a1 1 0 0 1 1-1zm3 5v3h6v-3z"/></svg>08 9000 4822</li>
    <li><svg viewBox="0 0 16 16" aria-hidden="true"><path d="M1 3h14v10H1zm1.5 1.2v.4L8 8.6l5.5-4v-.4zm0 2.2v5.4h11V6.4L8 10.3z"/></svg>sales@tarvoplastics.com.au</li>
  </ul>

  <div class="footer-rule"></div>
  <div class="footer-band">Kestrel Holdings Pty Ltd T/A Tarvo Plastics ABN: TBA</div>
</section>

<section class="card card-back" aria-label="Business card back">
  <div class="brand-back">
    <span class="brand-mark"></span>
    <span class="brand-name">Tarvo Plastics</span>
  </div>

  <p class="headline">The Products And Services That We Offer<br>Are Supplied From Diy To Trade &amp; Industrial Engineering Markets</p>

  <div class="offer-col services">
    <h2>We specialise in:</h2>
    <ul>
      <li>Cut to size panels (all shapes and sizes)</li>
      <li>Plastics fabrication &amp; Welding</li>
      <li>Custom Designs</li>
      <li>Plastic Repairs</li>
      <li>PVC Pipe Slotting &amp; PVC Pipe Threading</li>
      <li>Supplier of all types of engineering plastics and profiles</li>
    </ul>
  </div>

  <div class="divider-back"></div>

  <div class="offer-col materials">
    <h2>Including:</h2>
    <ul>
      <li>Acrylic / Clarvene</li>
      <li>Polycarbonate / Dorvil</li>
      <li>Prismatic Light Diffuser</li>
      <li>Vantrib</li>
      <li>HDPE / UHMWPE</li>
      <li>PVC / PVC Foam</li>
      <li>Nylon</li>
      <li>HIPS</li>
    </ul>
  </div>
</section>

</body>
</html>
```